wealth management firm, professional group, new model

we have a logo that works but we need a card, white background using our colors...clean look

our tag line if can be used in

The Bridge From Client to Owner

```html
<!DOCTYPE html>
<html lang="en">
<head>
<meta charset="utf-8">
<title>Verano Wealth Partners – Business Card</title>
<link rel="stylesheet" href="https://fonts.googleapis.com/css2?family=Montserrat:wght@400;500;800&display=swap">
<style>
  :root {
    --navy: #1f3560;
    --navy-deep: #192b4f;
    --ink: #17284a;
    --paper: #f6f6f4;
    --white: #ffffff;
    --backdrop: #2a2b2e;
  }
  * { box-sizing: border-box; margin: 0; padding: 0; }
  html, body {
    width: 1200px;
    height: 896px;
    overflow: hidden;
    background: var(--backdrop);
    font-family: "Montserrat", sans-serif;
  }
  .sheet {
    width: 1200px;
    height: 896px;
    display: flex;
    align-items: center;
    justify-content: center;
    gap: 44px;
  }
  .card {
    width: 525px;
    height: 300px;
    position: relative;
    overflow: hidden;
  }

  /* Front */
  .card-front {
    background: var(--paper);
    color: var(--ink);
    display: flex;
    flex-direction: column;
  }
  .front-brand {
    flex: 1;
    display: flex;
    flex-direction: column;
    align-items: center;
    justify-content: center;
    padding-top: 12px;
  }
  .brand-name {
    font-size: 52px;
    font-weight: 400;
    letter-spacing: 0.38em;
    margin-right: -0.38em;
    color: var(--ink);
    line-height: 1;
  }
  .brand-descriptor {
    margin-top: 16px;
    font-size: 17px;
    font-weight: 400;
    letter-spacing: 0.16em;
    color: var(--ink);
  }
  .tagline-band {
    height: 54px;
    background: var(--navy);
    color: var(--white);
    display: flex;
    align-items: center;
    justify-content: center;
    font-size: 14px;
    font-weight: 500;
    letter-spacing: 0.17em;
  }

  /* Back */
  .card-back {
    background: linear-gradient(160deg, var(--navy) 0%, var(--navy-deep) 100%);
    color: var(--white);
    display: flex;
    flex-direction: column;
    align-items: center;
    text-align: center;
    padding: 42px 36px 0;
  }
  .holder-name {
    font-size: 30px;
    font-weight: 800;
    letter-spacing: 0.13em;
    margin-right: -0.13em;
  }
  .holder-title {
    margin-top: 6px;
    font-size: 17px;
    font-weight: 400;
    letter-spacing: 0.03em;
  }
  .back-brand {
    margin-top: 32px;
    font-size: 24px;
    font-weight: 400;
    letter-spacing: 0.38em;
    margin-right: -0.38em;
  }
  .contact {
    margin-top: 30px;
    font-size: 14px;
    font-weight: 400;
    line-height: 1.5;
    letter-spacing: 0.02em;
  }
  .contact .divider { padding: 0 8px; }
</style>
</head>
<body>
  <main class="sheet">
    <section class="card card-front" aria-label="Card front">
      <div class="front-brand">
        <div class="brand-name">VERANO</div>
        <div class="brand-descriptor">WEALTH PARTNERS</div>
      </div>
      <div class="tagline-band">THE BRIDGE FROM CLIENT TO OWNER</div>
    </section>

    <section class="card card-back" aria-label="Card back">
      <div class="holder-name">JORDAN REYES</div>
      <div class="holder-title">Senior Wealth Advisor</div>
      <div class="back-brand">VERANO</div>
      <div class="contact">
        <div>jordan@veranowealth.com<span class="divider">|</span>+1(555) 610-4827</div>
        <div>veranowealth.com</div>
      </div>
    </section>
  </main>
</body>
</html>
```